sydney wedding photography business needs a business card design

we need a business card design for a sydney based wedding photography and videography business. our business name is :golden hour studio and film. our target clients are 24-35 yrs female. our style is candid, organic, natural, dynamic. we are a team of young photographers and videographers, and help brides to create memories that they will cherish for the rest of their lives. the logo will be provided. we want an elegant design that reflects our style, and also want to give a great impression to our clients that we are one of the best studios in sydney and our brand means quality and premium service.

Target Market(s)

bride to be, 24-35 years old, living in sydney and surrunding areas

Industry/Entity Type

Wedding Photography

Contact Information for Business Card

address: 57 tarrant street, glenmore nsw 2047
mobile: 0431872259
phone: (02) 9163 2408
info@tidewillowstudio.net.au
www.tidewillowstudio.net.au
facebook:tidewillowweddings
instagram:tidewillowweddings

Font styles to use
Serif
Sans Serif

Requirements
Nice to have
• maybe add my slogan"memories beyond eternity" if the layout looks good
Should not have
• no black color, not good idea for wedding biz card

```html
<!DOCTYPE html>
<html lang="en">
<head>
<meta charset="utf-8">
<title>golden hour studio and film — business card</title>
<link rel="stylesheet" href="https://fonts.googleapis.com/css2?family=Arimo:wght@400;700&display=swap">
<style>
  :root {
    --backdrop: #2b2b2d;
    --gold-light: #f2c744;
    --gold-mid: #dba61c;
    --gold-deep: #b88411;
    --ink: #2a1e0c;
    --espresso-light: #4a3518;
    --espresso: #3a2912;
    --espresso-deep: #2c1f0d;
    --text-light: #f6ecd6;
  }
  * { box-sizing: border-box; margin: 0; padding: 0; }
  html, body {
    width: 1200px; height: 950px; overflow: hidden;
    background: var(--backdrop);
    font-family: "Arimo", Arial, sans-serif;
  }
  .canvas { position: relative; width: 1200px; height: 950px; }

  .card {
    position: absolute;
    width: 700px; height: 400px;
    border-radius: 4px;
    box-shadow: 0 14px 30px rgba(0,0,0,.45);
    overflow: hidden;
  }

  /* Front */
  .card-front {
    left: 70px; top: 50px;
    background: radial-gradient(ellipse at 45% 40%, var(--gold-light) 0%, var(--gold-mid) 55%, var(--gold-deep) 100%);
    color: var(--ink);
  }
  .front-brand {
    position: absolute; left: 0; right: 0; top: 150px;
    text-align: center; white-space: nowrap;
    font-size: 38px; font-weight: 700; letter-spacing: .5px;
  }
  .front-rule {
    position: absolute; left: 200px; right: 200px; top: 232px;
    height: 1px; background: var(--ink); opacity: .55;
  }
  .front-dot {
    position: absolute; left: 340px; top: 222px;
    width: 20px; height: 20px; border-radius: 50%;
    background: var(--ink);
  }
  .front-handle {
    position: absolute; left: 0; right: 0; top: 252px;
    text-align: center; font-size: 15px; letter-spacing: .3px;
  }

  /* Back */
  .card-back {
    left: 430px; top: 500px;
    background: linear-gradient(160deg, var(--espresso-light) 0%, var(--espresso) 45%, var(--espresso-deep) 100%);
    color: var(--text-light);
  }
  .back-brand {
    position: absolute; left: 170px; right: 30px; top: 95px;
    text-align: center; white-space: nowrap;
    font-size: 32px; font-weight: 700;
    color: var(--gold-light);
  }
  .back-band {
    position: absolute; left: 0; right: 0; bottom: 0; height: 22px;
    background: linear-gradient(90deg, var(--gold-deep), var(--gold-light), var(--gold-mid));
  }
  .person { position: absolute; left: 40px; top: 228px; }
  .person-name { font-size: 20px; font-weight: 700; color: var(--gold-light); }
  .person-role { font-size: 15px; margin-top: 4px; }
  .contact-list { position: absolute; left: 40px; top: 290px; list-style: none; }
  .contact-list li {
    display: flex; align-items: center; gap: 10px;
    font-size: 15px; line-height: 24px; white-space: nowrap;
  }
  .contact-list svg { width: 16px; height: 16px; fill: var(--gold-light); flex: none; }
  .divider {
    position: absolute; left: 390px; top: 245px;
    width: 2px; height: 70px; background: var(--gold-mid);
  }
  .address {
    position: absolute; left: 410px; top: 240px;
    font-size: 15px; line-height: 24px; font-style: normal; white-space: nowrap;
  }
</style>
</head>
<body>
<main class="canvas">

  <section class="card card-front" aria-label="Card front">
    <p class="front-brand">golden hour studio and film</p>
    <span class="front-rule"></span>
    <span class="front-dot"></span>
    <p class="front-handle">tidewillowweddings</p>
  </section>

  <section class="card card-back" aria-label="Card back">
    <p class="back-brand">golden hour studio and film</p>

    <div class="person">
      <p class="person-name">Mara Ellison</p>
      <p class="person-role">President</p>
    </div>

    <ul class="contact-list">
      <li>
        <svg viewBox="0 0 16 16" aria-hidden="true"><path d="M3 1h3l1 4-2 1.5a9 9 0 0 0 4.5 4.5L11 9l4 1v3a2 2 0 0 1-2 2A12 12 0 0 1 1 3a2 2 0 0 1 2-2z"/></svg>
        (02) 9163 2408
      </li>
      <li>
        <svg viewBox="0 0 16 16" aria-hidden="true"><path d="M4.5 0h7A1.5 1.5 0 0 1 13 1.5v13a1.5 1.5 0 0 1-1.5 1.5h-7A1.5 1.5 0 0 1 3 14.5v-13A1.5 1.5 0 0 1 4.5 0zM5 2v10h6V2zm3 11a1 1 0 1 0 0 2 1 1 0 0 0 0-2z"/></svg>
        0431 872 259
      </li>
      <li>
        <svg viewBox="0 0 16 16" aria-hidden="true"><path d="M0 3h16v1.2L8 9 0 4.2zM0 5.6l8 4.8 8-4.8V13H0z"/></svg>
        info@tidewillowstudio.net.au
      </li>
    </ul>

    <span class="divider"></span>
    <address class="address">
      57 tarrant street<br>
      glenmore nsw 2047<br>
      www.tidewillowstudio.net.au
    </address>

    <span class="back-band"></span>
  </section>

</main>
</body>
</html>
```